Need business card with a logo for a hearing aid sales and audiology business. We have two Hearing Instrument Specialists and one Audiologist on staff. Over 25 years in business. Locally owned and operated. Financing available. Most insurances accepted.

Summit Audio Wellness LLC
48730 W Larchmont, Suite 7
Spokane, WA 99281
509-617-2084
www.summitaudiowell.example

Manager
Tobias Kerrell HIS COHC
License #71829046

Target Market(s)

50yr old + people with a hearing loss.

Industry/Entity Type

Business

Contact Information for Business Card

48730 W Larchmont, Suite 7
Spokane, WA 99281
509-617-2084
www.summitaudiowell.example

Manager
Tobias Kerrell HIS COHC
NLVE #71829046

Font styles to use
Serif
Sans Serif

Requirements
Must have
• Business name, Tobias's name and title(s) and contact information, License #, web address

```html
<!DOCTYPE html>
<html lang="en">
<head>
<meta charset="utf-8">
<title>Summit Audio Wellness LLC – Business Card</title>
<link rel="stylesheet" href="https://fonts.googleapis.com/css2?family=Open+Sans:wght@400;600;700&display=swap">
<style>
  :root {
    --page-bg: #ecebe8;
    --card-white: #ffffff;
    --brand-blue: #0b4fc4;
    --band-light: #0b8fd2;
    --band-deep: #0530c2;
    --band-top: #0a7fc9;
    --text-light: #ffffff;
  }
  * { box-sizing: border-box; margin: 0; padding: 0; }
  html, body { width: 1200px; height: 900px; overflow: hidden; }
  body {
    background: var(--page-bg);
    font-family: "Open Sans", Arial, sans-serif;
    position: relative;
  }
  .card {
    position: absolute;
    background: var(--card-white);
    overflow: hidden;
    box-shadow: 0 6px 18px rgba(0,0,0,0.18);
  }
  .card-front { left: 78px; top: 34px; width: 588px; height: 365px; }
  .card-back  { left: 388px; top: 506px; width: 567px; height: 352px; }

  .brand-name {
    color: var(--brand-blue);
    font-weight: 700;
    letter-spacing: 0.5px;
    white-space: nowrap;
  }
  .front-brand {
    position: absolute; left: 36px; top: 56px;
    display: flex; align-items: center; gap: 12px;
    font-size: 30px;
  }
  .brand-dot {
    width: 18px; height: 18px; border-radius: 50%;
    background: var(--brand-blue);
  }
  .info-band {
    position: absolute; left: 0; top: 155px; width: 100%; height: 210px;
    background: linear-gradient(180deg, var(--band-light) 0%, var(--band-deep) 100%);
    color: var(--text-light);
    padding: 12px 30px;
  }
  .person-name { font-size: 17px; font-weight: 600; }
  .person-creds { font-size: 14px; font-weight: 600; }
  .person-role { font-size: 15px; margin-top: 4px; }
  .license { font-size: 15px; font-weight: 600; margin-top: 16px; margin-left: 6px; }
  .contact-list { list-style: none; margin-top: 10px; font-size: 15px; }
  .contact-list li { display: flex; align-items: center; gap: 8px; line-height: 22px; }
  .contact-icon { width: 13px; height: 13px; flex: none; }
  .address { font-size: 15px; margin-top: 16px; }

  .back-top-band {
    position: absolute; left: 0; top: 0; width: 100%; height: 60px;
    background: var(--band-top);
  }
  .back-bottom-band {
    position: absolute; left: 0; bottom: 0; width: 100%; height: 61px;
    background: var(--band-deep);
  }
  .back-brand {
    position: absolute; left: 0; top: 60px; width: 100%; height: 231px;
    display: flex; flex-direction: column; align-items: center; justify-content: center; gap: 18px;
  }
  .back-brand .brand-dot { width: 40px; height: 40px; }
  .back-brand .brand-name { font-size: 27px; }
</style>
</head>
<body>

<section class="card card-front" aria-label="Business card front">
  <div class="front-brand">
    <span class="brand-dot"></span>
    <span class="brand-name">Summit Audio Wellness LLC</span>
  </div>
  <div class="info-band">
    <p class="person-name">Tobias Kerrell <span class="person-creds">HIS COHC</span></p>
    <p class="person-role">Manager</p>
    <p class="license">License #71829046</p>
    <ul class="contact-list">
      <li>
        <svg class="contact-icon" viewBox="0 0 24 24" aria-hidden="true"><path fill="#fff" d="M6.6 10.8a15.1 15.1 0 0 0 6.6 6.6l2.2-2.2c.3-.3.7-.4 1-.2 1.1.4 2.3.6 3.6.6.6 0 1 .4 1 1V20c0 .6-.4 1-1 1A17 17 0 0 1 3 4c0-.6.4-1 1-1h3.5c.6 0 1 .4 1 1 0 1.3.2 2.5.6 3.6.1.3 0 .7-.2 1z"/></svg>
        509-617-2084
      </li>
      <li>
        <svg class="contact-icon" viewBox="0 0 24 24" aria-hidden="true"><circle cx="12" cy="12" r="10" fill="none" stroke="#fff" stroke-width="2.4"/><path d="M2 12h20M12 2c3 3 3 17 0 20M12 2c-3 3-3 17 0 20" fill="none" stroke="#fff" stroke-width="1.8"/></svg>
        www.summitaudiowell.example
      </li>
    </ul>
    <p class="address">48730 W Larchmont, Suite 7 Spokane, WA 99281</p>
  </div>
</section>

<section class="card card-back" aria-label="Business card back">
  <div class="back-top-band"></div>
  <div class="back-brand">
    <span class="brand-dot"></span>
    <span class="brand-name">Summit Audio Wellness LLC</span>
  </div>
  <div class="back-bottom-band"></div>
</section>

</body>
</html>
```